VFX Company Business Card Design Project

The Kestrel Works is a decentralized Visual Effects Studio servicing the television and feature film industries.
Project Brief:
Take our logo that was previously designed on Pencil Harbor and make a double sided business card.
Requirements:
- Card MUST be double sided.
- Front of card MUST have the yellow part of our logo against the dark grey background.
- Back of card is completely up to the designer.
- Back of card must include the complete company logo.
Please follow these File Preparation guidelines:
http://printnook.ca/infopage?file=filetype_en&s=PrintNook_new&lang=en
Business

```html
<!DOCTYPE html>
<html lang="en">
<head>
<meta charset="utf-8">
<title>The Kestrel Works — Business Card</title>
<link rel="stylesheet" href="https://fonts.googleapis.com/css2?family=Josefin+Sans:wght@600;700&family=Questrial&display=swap">
<style>
  :root {
    --page: #ffffff;
    --card: #262626;
    --brand-yellow: #ffc928;
    --name: #ececec;
    --muted: #6e7d7d;
    --shadow: rgba(0, 0, 0, 0.35);
  }
  html, body {
    margin: 0;
    padding: 0;
    width: 1200px;
    height: 900px;
    overflow: hidden;
    background: var(--page);
  }
  .canvas {
    position: relative;
    width: 1200px;
    height: 900px;
  }
  .card-holder {
    position: absolute;
    width: 635px;
    height: 317px;
    filter: drop-shadow(0 3px 3px var(--shadow));
  }
  .card-holder--front { left: 309px; top: 108px; }
  .card-holder--back  { left: 308px; top: 480px; }
  .card {
    position: relative;
    width: 100%;
    height: 100%;
    background: var(--card);
  }
  .card--front {
    clip-path: polygon(63px 0, 100% 0, 100% 100%, 0 100%, 0 69px);
  }
  .card--back {
    clip-path: polygon(0 0, calc(100% - 65px) 0, 100% 69px, 100% 100%, 0 100%);
  }
  .front-wordmark {
    position: absolute;
    left: 0;
    right: 0;
    top: 130px;
    margin: 0;
    text-align: center;
    font-family: "Josefin Sans", sans-serif;
    font-weight: 700;
    font-size: 46px;
    color: var(--brand-yellow);
    letter-spacing: 1px;
  }
  .back-wordmark {
    position: absolute;
    left: 34px;
    top: 128px;
    width: 220px;
    margin: 0;
    text-align: center;
    font-family: "Josefin Sans", sans-serif;
    font-weight: 700;
    font-size: 31px;
    line-height: 1.1;
    color: var(--brand-yellow);
  }
  .person {
    position: absolute;
    left: 336px;
    top: 38px;
  }
  .person__name {
    margin: 0;
    font-family: "Josefin Sans", sans-serif;
    font-weight: 700;
    font-size: 25px;
    color: var(--name);
    letter-spacing: 0.5px;
  }
  .person__title {
    margin: 8px 0 0;
    font-family: "Questrial", sans-serif;
    font-size: 18px;
    color: var(--muted);
    letter-spacing: 5.6px;
  }
  .contact {
    position: absolute;
    left: 337px;
    top: 210px;
    margin: 0;
    padding: 0;
    list-style: none;
    font-family: "Questrial", sans-serif;
    font-size: 17px;
    line-height: 23px;
    color: var(--muted);
    letter-spacing: 1.8px;
  }
</style>
</head>
<body>
<main class="canvas">
  <div class="card-holder card-holder--front">
    <section class="card card--front" aria-label="Card front">
      <p class="front-wordmark">The Kestrel Works</p>
    </section>
  </div>

  <div class="card-holder card-holder--back">
    <section class="card card--back" aria-label="Card back">
      <p class="back-wordmark">The Kestrel Works</p>
      <div class="person">
        <h1 class="person__name">DANIEL MERCER</h1>
        <p class="person__title">Creative Director</p>
      </div>
      <ul class="contact">
        <li>dmercer@kestrelworks.com</li>
        <li>(510) 555-0142</li>
        <li>KESTRELWORKS.COM</li>
      </ul>
    </section>
  </div>
</main>
</body>
</html>
```